Communication and Marketing agency needs a new presentation card

We are a group of communication and marketing agencies specialized in companies that are in the logistics and industrial sector. The head agency is TELVANO Grupo and the group consists of 4 agencies: TELVANO Media, TELVANO Digital, TELVANO Research and DifundeEnPantalla. We hace 4 offices in Spain (Madrid, Barcelona, Valencia and Murcia). We are looking for a clean and attractive design that transmits our experience, brand presence in the market and knowledge to those who receive the card.It has to maintain the colors of the logo that is attached.
Target Market(s)
logistics and industrial sector
Marketing department
Contact Information for Business Card
Clean and attractive design

```html
<!DOCTYPE html>
<html lang="es">
<head>
<meta charset="utf-8">
<title>TELVANO Grupo – Tarjetas de presentación</title>
<link rel="stylesheet" href="https://fonts.googleapis.com/css2?family=Open+Sans:wght@400;600;700&display=swap">
<style>
  :root {
    --brand-red: #b81f2a;
    --brand-red-light: #c42a36;
    --brand-red-dark: #a51a24;
    --ink: #3a3a3a;
    --muted: #5a5a5a;
    --paper: #ffffff;
    --backdrop: #2b2b2b;
    --divider: #c9c9c9;
  }
  * { box-sizing: border-box; margin: 0; padding: 0; }
  html, body {
    width: 1200px; height: 892px; overflow: hidden;
    background: var(--backdrop);
    font-family: "Open Sans", Arial, sans-serif;
  }
  .canvas { position: relative; width: 1200px; height: 892px; }

  .card {
    position: absolute; width: 560px; height: 340px; overflow: hidden;
    box-shadow: 0 10px 30px rgba(0,0,0,.45);
  }

  /* Front */
  .card--front {
    left: 60px; top: 70px;
    background: linear-gradient(160deg, var(--brand-red-light), var(--brand-red-dark));
  }
  .front__brand {
    position: absolute; left: 0; right: 0; top: 96px;
    text-align: center; color: var(--paper);
  }
  .front__brand-name {
    font-size: 44px; font-weight: 400; letter-spacing: 3px; line-height: 1;
  }
  .front__agencies {
    position: absolute; left: 0; right: 0; top: 226px; height: 66px;
    background: var(--paper);
    display: grid; grid-template-columns: repeat(4, 1fr);
    align-items: center; padding: 0 12px;
  }
  .agency {
    font-size: 12px; font-weight: 400; letter-spacing: .3px;
    white-space: nowrap; text-align: center;
  }
  .agency--grey { color: var(--ink); }
  .agency--red { color: var(--brand-red); }

  /* Back */
  .card--back {
    left: 580px; top: 480px; background: var(--paper);
  }
  .back__logo {
    position: absolute; left: 36px; top: 124px;
    color: var(--brand-red); font-size: 26px; font-weight: 400;
    letter-spacing: 2px; line-height: 1; white-space: nowrap;
  }
  .back__divider {
    position: absolute; left: 296px; top: 36px; width: 1px; height: 170px;
    background: linear-gradient(to bottom, transparent, var(--divider) 20%, var(--divider) 80%, transparent);
  }
  .contact { position: absolute; left: 318px; top: 42px; }
  .contact__name {
    color: var(--brand-red); font-size: 19px; font-weight: 700; line-height: 1.1;
  }
  .contact__role {
    color: var(--muted); font-size: 13px; margin-bottom: 10px;
  }
  .contact__list { list-style: none; }
  .contact__item {
    display: flex; align-items: center; gap: 9px;
    color: var(--muted); font-size: 13px; line-height: 21px; white-space: nowrap;
  }
  .contact__icon { width: 13px; height: 13px; flex: none; fill: var(--brand-red); }

  .back__band {
    position: absolute; left: 0; right: 0; top: 250px; height: 46px;
    background: var(--brand-red);
    display: flex; align-items: center; justify-content: flex-end;
    padding-right: 34px;
    color: var(--paper); font-size: 14px; font-weight: 600; letter-spacing: .3px;
  }
  .back__band .dot { margin: 0 7px; }
</style>
</head>
<body>
<main class="canvas">

  <section class="card card--front" aria-label="Anverso de la tarjeta">
    <div class="front__brand">
      <p class="front__brand-name">TELVANO Grupo</p>
    </div>
    <div class="front__agencies">
      <span class="agency agency--grey">TELVANO Digital</span>
      <span class="agency agency--red">TELVANO Media</span>
      <span class="agency agency--grey">TELVANO Research</span>
      <span class="agency agency--red">DifundeEnPantalla</span>
    </div>
  </section>

  <section class="card card--back" aria-label="Reverso de la tarjeta">
    <p class="back__logo">TELVANO Media</p>
    <div class="back__divider"></div>

    <div class="contact">
      <p class="contact__name">Adrián Velasco</p>
      <p class="contact__role">Director</p>
      <ul class="contact__list">
        <li class="contact__item">
          <svg class="contact__icon" viewBox="0 0 16 16" aria-hidden="true"><path d="M3 1h3l1.5 4-2 1.3a9 9 0 0 0 4.2 4.2L11 8.5l4 1.5v3a2 2 0 0 1-2 2A12 12 0 0 1 1 3a2 2 0 0 1 2-2z"/></svg>
          910 555 214
        </li>
        <li class="contact__item">
          <svg class="contact__icon" viewBox="0 0 16 16" aria-hidden="true"><path d="M4 0h8a1 1 0 0 1 1 1v14a1 1 0 0 1-1 1H4a1 1 0 0 1-1-1V1a1 1 0 0 1 1-1zm1 2v10h6V2zm3 11a1 1 0 1 0 0 2 1 1 0 0 0 0-2z"/></svg>
          600 555 781
        </li>
        <li class="contact__item">
          <svg class="contact__icon" viewBox="0 0 16 16" aria-hidden="true"><path d="M0 3h16v10H0zm1.5 1.2v.3L8 9l6.5-4.5v-.3z"/></svg>
          avelasco@telvano.es
        </li>
        <li class="contact__item">
          <svg class="contact__icon" viewBox="0 0 16 16" aria-hidden="true"><rect x="1" y="1" width="14" height="14" rx="2"/></svg>
          adrianvelasco
        </li>
        <li class="contact__item">
          <svg class="contact__icon" viewBox="0 0 16 16" aria-hidden="true"><circle cx="8" cy="8" r="7"/></svg>
          telvano.es
        </li>
      </ul>
    </div>

    <div class="back__band">
      Madrid<span class="dot">•</span>Barcelona<span class="dot">•</span>Valencia<span class="dot">•</span>Murcia
    </div>
  </section>

</main>
</body>
</html>
```